Building Design company needing a letterhead

We need a letter head for our Building Design company to send letters etc. to our clients, consultants, councils etc. We would like to see our logo used and company colours. I have attached our style guide and an example of our current letterheads. Top left we would like our logo, top right we would like the company details and at the footer we would like some sort of image/design etc. that suits our brand. I like the Tarrow Design letterhead attached.

Target Market(s)

Professionals, Councils, Consultants, Mums & Dads

Industry/Entity Type

Architecture

Other font styles liked:
• refer the design style guide

Colors
f37122
000000
1b1b1b

Requirements
Must have
• Must have the minimum of a logo, company details and footer
Nice to have
• An image/design made for the footer that would suite our brand and website at www.corvanplans.com.au. Also it would be nice to include the KMEOT logo somewhere perhaps included in the footer.
Should not have
• Large images in the header. I just want the logo and company details.

```html
<!DOCTYPE html>
<html lang="en">
<head>
<meta charset="utf-8">
<title>Corvan Plans Letterhead</title>
<link rel="stylesheet" href="https://fonts.googleapis.com/css2?family=Arimo:wght@400;700&family=Fira+Sans:wght@500&display=swap">
<style>
  :root {
    --backdrop: #5c4c43;
    --paper: #ffffff;
    --ink: #1b1b1b;
    --text: #3a3a3a;
    --accent: #f37122;
  }
  * { margin: 0; padding: 0; box-sizing: border-box; }
  html, body {
    width: 967px;
    height: 1200px;
    overflow: hidden;
    background: var(--backdrop);
  }
  .letterhead {
    position: absolute;
    left: 135px;
    top: 133px;
    width: 720px;
    height: 932px;
    background: var(--paper);
  }
  .brand {
    position: absolute;
    left: 30px;
    top: 32px;
    display: flex;
    align-items: center;
    gap: 16px;
  }
  .brand-square {
    width: 54px;
    height: 54px;
    background: var(--accent);
  }
  .brand-name {
    font-family: "Fira Sans", sans-serif;
    font-weight: 500;
    font-size: 38px;
    line-height: 38px;
    letter-spacing: 1px;
    color: var(--ink);
    text-transform: uppercase;
  }
  .company-details {
    position: absolute;
    right: 30px;
    top: 35px;
    text-align: right;
    font-family: "Arimo", Arial, sans-serif;
    font-size: 12px;
    line-height: 16.5px;
    color: var(--text);
  }
  .company-details .contact-line {
    font-weight: 700;
    color: var(--accent);
  }
  .footer-mark {
    position: absolute;
    right: 0;
    bottom: 0;
    display: flex;
    align-items: flex-end;
    gap: 8px;
  }
  .footer-name {
    font-family: "Fira Sans", sans-serif;
    font-weight: 500;
    font-size: 14px;
    color: var(--ink);
    text-transform: uppercase;
    letter-spacing: 1px;
    margin-bottom: 4px;
  }
  .footer-square {
    width: 84px;
    height: 90px;
    background: var(--accent);
  }
</style>
</head>
<body>
  <main class="letterhead">
    <header>
      <div class="brand">
        <div class="brand-square"></div>
        <div class="brand-name">Corvan<br>Plans</div>
      </div>
      <address class="company-details" style="font-style:normal">
        <div>admin@corvanplans.com.au</div>
        <div>www.corvanplans.com.au</div>
        <div>Unit 4/22 Ferrow Way Lakeview WA 6180</div>
        <div>PO Box 3187 Lakeview North WA 6180</div>
        <div class="contact-line">PH (08) 6000 4821 ABN 47 612 308 914</div>
      </address>
    </header>
    <footer class="footer-mark">
      <div class="footer-name">Corvan Plans</div>
      <div class="footer-square"></div>
    </footer>
  </main>
</body>
</html>
```